Harborline Renewal Business Card Design

Professional and clean design. The design colors should flow with the logo. Two-sided card with the website on the back which is:

www.HarborlineRenewal.example.

"Specializing in Water Damage Restoration"

On the front I need the name, email, phone, and logo.

Name: Darnell Quisby
Email: Darnell@HarborlineRenewal.example
Phone: 555-318-2046 for now

I only have the Preview and Thumbnail right now but should have the source files uploaded within a day or two.

Target Market(s)

Flood victims, home owners with water damage from busted pipes etc...

Industry/Entity Type

Business

Contact Information for Business Card

Name: Darnell Quisby

Font styles to use
Serif
Sans Serif

Requirements
Must have
• Business Card Details Info

```html
<!DOCTYPE html>
<html lang="en">
<head>
<meta charset="utf-8">
<title>Harborline Renewal – Business Card</title>
<link rel="stylesheet" href="https://fonts.googleapis.com/css2?family=Cinzel:wght@500;600&family=Arimo:wght@700&family=Source+Sans+3:wght@400&display=swap">
<style>
  :root {
    --stage: #e9e6e1;
    --card: #545454;
    --blue: #2a93d5;
    --blue-light: #5bc2ef;
    --white: #ffffff;
  }
  * { margin: 0; padding: 0; box-sizing: border-box; }
  html, body { width: 960px; height: 1200px; overflow: hidden; }
  body { background: var(--stage); position: relative; }

  .card {
    position: absolute;
    left: 105px;
    width: 751px;
    height: 458px;
    background: var(--card);
    overflow: hidden;
  }
  .card--back { top: 58px; }
  .card--front { top: 684px; }

  .stripe { position: absolute; left: 0; width: 100%; }
  .stripe--1 { top: 0; height: 8px; background: var(--blue); }
  .stripe--2 { top: 14px; height: 8px; background: var(--blue-light); }
  .stripe--3 { top: 29px; height: 8px; background: var(--blue); }
  .band-bottom { position: absolute; left: 0; bottom: 0; width: 100%; height: 36px; background: var(--blue); }

  /* back side */
  .back-mark {
    position: absolute; left: 0; top: 150px; width: 100%;
    display: flex; align-items: center; justify-content: center; gap: 18px;
  }
  .mark-dot { width: 54px; height: 54px; border-radius: 50%; background: var(--blue-light); flex: none; }
  .mark-name {
    font-family: "Cinzel", serif; font-weight: 600; color: var(--blue);
    font-size: 40px; letter-spacing: 2px; line-height: 1.05; text-transform: uppercase;
  }
  .back-url {
    position: absolute; left: 0; top: 300px; width: 100%; text-align: center;
    font-family: "Source Sans 3", sans-serif; color: var(--white); font-size: 28px;
  }

  /* front side */
  .person-name {
    position: absolute; left: 45px; top: 92px;
    font-family: "Cinzel", serif; font-weight: 500; color: var(--white);
    font-size: 32px; letter-spacing: 1px; text-transform: uppercase;
  }
  .contact { position: absolute; left: 45px; display: flex; align-items: center; gap: 20px; }
  .contact--phone { top: 174px; }
  .contact--email { top: 257px; }
  .contact--web { top: 333px; }
  .contact svg { width: 26px; height: 26px; flex: none; }
  .contact-text { font-family: "Arimo", sans-serif; font-weight: 700; color: var(--white); font-size: 14.5px; }

  .front-mark {
    position: absolute; left: 450px; top: 120px; width: 240px;
    display: flex; flex-direction: column; align-items: center; gap: 18px;
  }
  .front-mark .mark-dot { width: 150px; height: 150px; }
  .front-mark .mark-name { font-size: 34px; text-align: center; }
</style>
</head>
<body>

  <section class="card card--back" aria-label="Card back">
    <div class="stripe stripe--1"></div>
    <div class="stripe stripe--2"></div>
    <div class="stripe stripe--3"></div>
    <div class="back-mark">
      <span class="mark-dot"></span>
      <span class="mark-name">Harborline<br>Renewal</span>
    </div>
    <p class="back-url">www.HarborlineRenewal.example</p>
    <div class="band-bottom"></div>
  </section>

  <section class="card card--front" aria-label="Card front">
    <div class="stripe stripe--1"></div>
    <div class="stripe stripe--2"></div>
    <div class="stripe stripe--3"></div>

    <h1 class="person-name">Darnell Quisby</h1>

    <div class="contact contact--phone">
      <svg viewBox="0 0 24 24" aria-hidden="true"><path fill="#fff" d="M6.6 2.5c.6-.4 1.4-.3 1.8.3l2.2 3.2c.4.6.3 1.4-.2 1.8L9 9c.9 2.3 3.3 4.8 5.9 6l1.3-1.4c.5-.5 1.3-.6 1.8-.2l3.2 2.2c.6.4.7 1.2.3 1.8l-1.3 2c-.7 1-2 1.5-3.2 1.1C10.6 18.5 5.3 13.3 3.4 7c-.4-1.2.1-2.5 1.1-3.2z"/></svg>
      <span class="contact-text">555-318-2046</span>
    </div>

    <div class="contact contact--email">
      <svg viewBox="0 0 24 24" aria-hidden="true"><rect x="2" y="5" width="20" height="14" fill="none" stroke="#fff" stroke-width="2"/><path d="M2 5l10 8 10-8M2 19l7.5-7M22 19l-7.5-7" fill="none" stroke="#fff" stroke-width="2"/></svg>
      <span class="contact-text">Darnell@HarborlineRenewal.example</span>
    </div>

    <div class="contact contact--web">
      <svg viewBox="0 0 24 24" aria-hidden="true"><g fill="none" stroke="#fff" stroke-width="1.8"><circle cx="11" cy="11" r="9"/><ellipse cx="11" cy="11" rx="4" ry="9"/><path d="M2 11h18M4 6h14M4 16h14"/></g><path d="M14 13l7 4-3 1 2 3-1.5 1-2-3-2.5 2z" fill="#fff" stroke="#545454" stroke-width="1"/></svg>
      <span class="contact-text">www.HarborlineRenewal.example</span>
    </div>

    <div class="front-mark">
      <span class="mark-dot"></span>
      <span class="mark-name">Harborline<br>Renewal</span>
    </div>

    <div class="band-bottom"></div>
  </section>

</body>
</html>
```